Hunting Forty Book Cover

Book cover for both print paperback and ebook versions of a collection of short stories. Publisher is Quiet Heron Publishers. The cover needs to capture the essence of the title concept to be chosen. Print cover template is attached as well as logo file. The book title is "Hunting Forty, Short Stories by Rob T. Verell"

The concept is related to the movie Copper Wasp, where character Percy Drummage explains his amps are louder because they go to eleven. If you are not familiar, go to vidstreamo and search for "Copper Wasp, eleven" to see the scene. The concept can also be explained as a person who persists in a belief or behavior in spite of overwhelming evidence it makes little sense.

Target Market(s)

Adult fiction, short stories,

Font styles to use
Serif

Colors

Designer to choose colors to be used in the design.

Requirements
Must have
• Must be more than the obvious amp dial, showing it goes to eleven. It should be a creative take on the concept.
Nice to have
• Possible Ideas;
• - person betting all-in on an inside straight (cards showing, pushing chips forward..)
• - some creative play on the amp dials
Should not have
• Do not provide artwork with elements we have to arrange for an extra license. AI compatible files only.

```html
<!DOCTYPE html>
<html lang="en">
<head>
<meta charset="utf-8">
<title>Hunting Forty — Cover Wrap</title>
<link rel="stylesheet" href="https://fonts.googleapis.com/css2?family=Bebas+Neue&family=Libre+Baskerville&family=Lora&display=swap">
<style>
  :root {
    --ink: #181818;
    --paper: #ffffff;
    --shadow-tone: #222222;
    --light-tone: #6a6a6a;
    --brand: #1f7a45;
  }
  * { margin: 0; padding: 0; box-sizing: border-box; }
  html, body { width: 1200px; height: 878px; overflow: hidden; background: var(--ink); }
  .cover-wrap { position: relative; width: 1200px; height: 878px; background: var(--ink); color: var(--paper); overflow: hidden; }

  /* Back cover */
  .back-title {
    position: absolute; left: 0; width: 580px; top: 48px; text-align: center;
    font-family: "Bebas Neue", sans-serif; font-size: 58px; letter-spacing: 3px; line-height: 1;
  }
  .back-byline {
    position: absolute; left: 0; width: 548px; top: 114px; text-align: center;
    font-family: "Libre Baskerville", serif; font-size: 21px; letter-spacing: 5px;
  }
  .blurb {
    position: absolute; left: 55px; width: 470px;
    font-family: "Lora", serif; font-size: 16.4px; line-height: 20.7px;
  }
  .blurb--first { top: 195px; }
  .blurb--second { top: 512px; }

  .imprint { position: absolute; display: flex; align-items: center; gap: 5px; font-family: "Lora", serif; color: var(--brand); }
  .imprint__mark { width: 12px; height: 12px; background: var(--brand); flex: none; }
  .imprint--back { left: 43px; top: 790px; font-size: 10px; width: 90px; line-height: 1.15; }
  .imprint--spine { left: 578px; top: 790px; font-size: 8px; width: 52px; line-height: 1.15; flex-direction: column; align-items: flex-start; gap: 3px; }

  /* Spine */
  .spine-title, .spine-author {
    position: absolute; left: 601px; transform-origin: 0 0; transform: rotate(90deg); white-space: nowrap;
  }
  .spine-title { top: 76px; font-family: "Bebas Neue", sans-serif; font-size: 50px; line-height: 1; letter-spacing: 2px; transform: rotate(90deg) translateY(-50%); }
  .spine-author { top: 476px; font-family: "Libre Baskerville", serif; font-size: 24px; letter-spacing: 8px; line-height: 1; transform: rotate(90deg) translateY(-50%); }

  /* Front cover */
  .front-portrait {
    position: absolute; left: 635px; top: 60px; width: 565px; height: 818px;
    background:
      radial-gradient(ellipse 120px 170px at 58% 28%, var(--light-tone), transparent 75%),
      radial-gradient(ellipse 300px 420px at 62% 80%, var(--shadow-tone), transparent 80%);
  }
  .front-title {
    position: absolute; left: 760px; width: 335px; top: 428px;
    font-family: "Bebas Neue", sans-serif; font-size: 114px; line-height: 90px; letter-spacing: 3px; text-align: center;
  }
  .front-author {
    position: absolute; left: 740px; width: 380px; top: 778px; text-align: center;
    font-family: "Libre Baskerville", serif; font-size: 36px; letter-spacing: 12px; line-height: 1;
  }
</style>
</head>
<body>
<main class="cover-wrap">
  <section class="back-cover">
    <h2 class="back-title">HUNTING FORTY</h2>
    <p class="back-byline">BY ROB T. VERELL</p>
    <p class="blurb blurb--first">Lorem ipsum dolor sit amet, consectetur adipiscing elit, sed do eiusmod tempor incididunt ut labore et dolore magna aliqua. Nunc congue nisi vitae suscipit tellus mauris a diam maecenas. Enim lobortis scelerisque fermentum dui faucibus in ornare quam viverra. Malesuada bibendum arcu vitae elementum curabitur. Viverra suspendisse potenti nullam ac tortor vitae. Sed felis eget velit aliquet sagittis id consectetur purus. Nullam non nisi est sit amet facilisis magna etiam. Metus aliquam eleifend mi in nulla posuere sollicitudin aliquam. Habitasse platea dictumst quisque sagittis purus sit. Malesuada proin</p>
    <p class="blurb blurb--second">Augue eget arcu dictum varius duis at. Ullamcorper eget nulla facilisi etiam dignissim diam quis. Vitae aliquet nec ullamcorper sit amet risus nullam. Pulvinar neque laoreet suspendisse interdum consectetur libero id faucibus. Gravida dictum fusce ut placerat orci nulla pellentesque dignissim enim. Nibh tellus molestie nunc non blandit massa enim nec dui. Ultrices eros in cursus turpis massa tincidunt.</p>
    <div class="imprint imprint--back"><span class="imprint__mark"></span><span>Quiet Heron Publishers</span></div>
  </section>

  <section class="spine">
    <h2 class="spine-title">HUNTING FORTY</h2>
    <p class="spine-author">ROB T. VERELL</p>
    <div class="imprint imprint--spine"><span class="imprint__mark"></span><span>Quiet Heron</span></div>
  </section>

  <section class="front-cover">
    <div class="front-portrait" role="img" aria-label="Black and white portrait of a man in a dark suit, seen in profile from over his shoulder"></div>
    <h1 class="front-title">HUNTING<br>FORTY</h1>
    <p class="front-author">ROB T. VERELL</p>
  </section>
</main>
</body>
</html>
```